Harborview Estates Business Card for Apartment Buildings

Create business cards for resident managers who run apartment buildings. The audience is the public who are searching for apartment rentals, and current residents who live at the apartment building. Key design element will be incorporating the company logo, however, the logo cannot dominate. The building name and manager name are more important than the logo. Current business card design leaves little room for copy, so we may need to reduce the size on the current card to allow for more space for copy.

Target Market(s)

Adults 18-65 years of age, who are looking for an apartment rental, plus current residents who live at our apartment buildings.

Industry/Entity Type

Property Management

Contact Information for Business Card

A major design element will be use of the company logo. Important property and manager contact information must be part of the design. The size of the logo will need to be reduced to make room for building and manager contact copy.

Font styles to use
Sans Serif

Colors
3176b5
000000
959595
ffffff

Requirements
Must have
• 1) Incorporate the company logo.
• 2) Use the company colors (dark blue, black/grey, over white).
• 3) FEATURE THE BUILDING NAME
• 4) FEATURE THE MANAGER NAME
• 5) The company name is less important than BUILDING and MANAGER
• 6) Manager contact information
• **SEE ATTACHED CREATIVE BRIEF**
Nice to have
• 1) Back of card logo watermark
• 2) Ability to write notes on back of carfd
Should not have
• Avoid letting the company logo dominate the card, the building name and manager are more important than the company logo.

```html
<!DOCTYPE html>
<html lang="en">
<head>
<meta charset="utf-8">
<title>Harborview Estates – Business Card</title>
<link href="https://fonts.googleapis.com/css2?family=Lato:wght@400;700&display=swap" rel="stylesheet">
<style>
  :root {
    --brand-blue: #1f6aa8;
    --ink: #2b2b2b;
    --text: #1e1e1e;
    --grey: #959595;
    --paper: #ffffff;
    --backdrop: #2e2e2e;
  }
  * { margin: 0; padding: 0; box-sizing: border-box; }
  html, body {
    width: 1200px; height: 900px; overflow: hidden;
    background: var(--backdrop);
    font-family: "Lato", Arial, sans-serif;
  }
  .stage { position: relative; width: 1200px; height: 900px; }
  .card {
    position: absolute; top: 306px; width: 439px; height: 271px;
    background: var(--paper);
    box-shadow: 3px 4px 8px rgba(0,0,0,.55);
    overflow: hidden;
  }
  .card--front { left: 149px; }
  .card--back { left: 609px; }

  .name-tab { position: absolute; left: 0; top: 26px; width: 30px; height: 37px; }
  .manager-name {
    position: absolute; left: 33px; top: 27px;
    font-size: 20px; font-weight: 700; color: var(--brand-blue); letter-spacing: .2px;
  }
  .manager-title {
    position: absolute; left: 33px; top: 48px;
    font-size: 12px; color: var(--text);
  }

  .company {
    position: absolute; right: 25px; top: 104px;
    display: flex; align-items: center; gap: 10px;
  }
  .company__mark { width: 14px; height: 14px; background: var(--brand-blue); }
  .company__name {
    font-size: 24px; font-weight: 700; color: var(--brand-blue);
    line-height: 1.05; text-transform: uppercase; text-align: right;
  }

  .contact-list {
    position: absolute; left: 28px; top: 179px; list-style: none;
    font-size: 12px; color: var(--text); line-height: 16px;
  }
  .contact-list li { display: flex; align-items: center; gap: 5px; }
  .contact-list svg { width: 10px; height: 10px; fill: var(--brand-blue); }

  .address {
    position: absolute; right: 25px; top: 212px;
    font-size: 12px; color: var(--text); text-align: right; line-height: 16px; font-style: normal;
  }

  .footer-band { position: absolute; left: 0; bottom: 0; width: 439px; height: 20px; }

  .back-web {
    position: absolute; left: 0; right: 0; top: 214px;
    text-align: center; font-size: 12px; color: var(--text);
  }
</style>
</head>
<body>
<main class="stage">

  <section class="card card--front" aria-label="Business card front">
    <svg class="name-tab" viewBox="0 0 30 37" aria-hidden="true">
      <polygon points="2,0 14,0 16,37 0,37" fill="var(--brand-blue)"/>
      <polygon points="15,0 30,0 30,37 17,37" fill="var(--ink)"/>
    </svg>
    <h1 class="manager-name">DANIEL BROOKS</h1>
    <p class="manager-title">Property Manager</p>

    <div class="company">
      <span class="company__mark" aria-hidden="true"></span>
      <p class="company__name">Harborview<br>Estates LLC</p>
    </div>

    <ul class="contact-list">
      <li><svg viewBox="0 0 10 10"><path d="M1 4 Q5 0 9 4 L8 5 L6.5 4 V3 Q5 2.5 3.5 3 V4 L2 5 Z M2 6 H8 V9 H2 Z"/></svg>555-014-2278</li>
      <li><svg viewBox="0 0 10 10"><path d="M2.5 0.5 H7.5 V3 H2.5 Z M0.5 3.5 H9.5 V7.5 H8 V6 H2 V7.5 H0.5 Z M2.5 6.5 H7.5 V9.5 H2.5 Z"/></svg>555-014-3391</li>
      <li><svg viewBox="0 0 10 10"><path d="M0.5 2 H9.5 V8 H0.5 Z" /><path d="M0.5 2 L5 5.5 L9.5 2" fill="none" stroke="#fff" stroke-width="1"/></svg>daniel@harborviewestates.us</li>
      <li><svg viewBox="0 0 10 10"><circle cx="5" cy="5" r="4.5"/><path d="M2 4 Q4 3 4.5 5 Q6 6 5 8.5 M6 1.5 Q7 3 8.5 3.5" fill="none" stroke="#fff" stroke-width=".9"/></svg>www.harborviewestates.us</li>
    </ul>

    <address class="address">2208 Linden Crest Road #B210<br>Bayfield, CA 92000</address>

    <svg class="footer-band" viewBox="0 0 439 20" aria-hidden="true">
      <polygon points="0,6 215,6 205,20 0,20" fill="var(--brand-blue)"/>
      <polygon points="225,0 439,0 439,20 210,20" fill="var(--ink)"/>
    </svg>
  </section>

  <section class="card card--back" aria-label="Business card back">
    <p class="back-web">www.harborviewestates.us</p>
    <svg class="footer-band" viewBox="0 0 439 20" aria-hidden="true">
      <polygon points="0,6 215,6 205,20 0,20" fill="var(--brand-blue)"/>
      <polygon points="225,0 439,0 439,20 210,20" fill="var(--ink)"/>
    </svg>
  </section>

</main>
</body>
</html>
```